Business card por a urban DJ, up scale audience target

Need a sober design, modern, conservative colors but i can consider some options, y play rnb, hip hop, EDM and top40.

Business card for contact and personal info, double sided, use logo attrached please; im 42 so i need a card acording to my age an target audience.

Target Market(s)

Adult people, up scale audience

Industry/Entity Type

Music Download

Contact Information for Business Card

Cel (318) 4207265518 www.lumadrift.com

Requirements
Must have
• open mind
Nice to have
• open mind
Should not have
• DJ

```html
<!DOCTYPE html>
<html lang="en">
<head>
<meta charset="utf-8">
<title>Lumadrift Business Card</title>
<link rel="stylesheet" href="https://fonts.googleapis.com/css2?family=Jost:wght@400;500;700&display=swap">
<style>
  :root {
    --backdrop: #3b3e43;
    --card-white: #f7f7f7;
    --card-black: #171717;
    --ink: #1a1a1a;
    --ink-soft: #555555;
    --rule: #c9c9c9;
    --paper-white: #ffffff;
  }
  * { margin: 0; padding: 0; box-sizing: border-box; }
  html, body {
    width: 1200px;
    height: 750px;
    overflow: hidden;
    background: var(--backdrop);
    font-family: "Jost", sans-serif;
  }
  .stage {
    position: relative;
    width: 1200px;
    height: 750px;
  }
  .card {
    position: absolute;
    top: 228px;
    width: 462px;
    height: 263px;
    overflow: hidden;
  }
  .card--front {
    left: 124px;
    background: linear-gradient(180deg, var(--paper-white) 0%, var(--card-white) 100%);
  }
  .card--back {
    left: 618px;
    background: var(--card-black);
  }
  .front-band {
    position: absolute;
    left: 0; right: 0; bottom: 0;
    height: 19px;
    background: var(--card-black);
    border-top: 2px solid var(--rule);
  }
  .front-mark {
    position: absolute;
    left: 62px;
    top: 104px;
    width: 148px;
    text-align: center;
    font-size: 52px;
    font-weight: 700;
    line-height: 1;
    letter-spacing: 2px;
    color: var(--ink);
  }
  .front-divider {
    position: absolute;
    left: 236px;
    top: 86px;
    width: 1px;
    height: 98px;
    background: var(--rule);
  }
  .contact {
    position: absolute;
    left: 263px;
    top: 90px;
  }
  .contact__name {
    font-size: 18px;
    font-weight: 500;
    color: var(--ink);
    line-height: 1.2;
  }
  .contact__title {
    font-size: 14px;
    font-weight: 400;
    color: var(--ink-soft);
    line-height: 1.3;
  }
  .contact__list {
    list-style: none;
    margin-top: 12px;
  }
  .contact__item {
    display: flex;
    align-items: center;
    gap: 6px;
    font-size: 13.5px;
    color: var(--ink-soft);
    line-height: 1.4;
  }
  .contact__icon { width: 11px; height: 13px; flex: none; }
  .back-mark {
    position: absolute;
    left: 0; right: 0;
    top: 78px;
    text-align: center;
    font-size: 80px;
    font-weight: 700;
    line-height: 1;
    letter-spacing: 3px;
    color: var(--paper-white);
  }
  .back-url {
    position: absolute;
    left: 0; right: 0;
    top: 182px;
    text-align: center;
    font-size: 10.5px;
    font-weight: 700;
    letter-spacing: 2.2px;
    color: var(--paper-white);
  }
</style>
</head>
<body>
<main class="stage">
  <section class="card card--front">
    <div class="front-mark">LUMA</div>
    <div class="front-divider"></div>
    <div class="contact">
      <p class="contact__name">MARCUS HALE</p>
      <p class="contact__title">CEO/FOUNDER</p>
      <ul class="contact__list">
        <li class="contact__item">
          <svg class="contact__icon" viewBox="0 0 11 13" aria-hidden="true">
            <rect x="1.5" y="0.5" width="8" height="12" rx="1.2" fill="none" stroke="#1a1a1a" stroke-width="1.4"/>
            <rect x="3.5" y="2.5" width="4" height="6" fill="#1a1a1a"/>
          </svg>
          (318) 4207265518
        </li>
        <li class="contact__item">
          <svg class="contact__icon" viewBox="0 0 11 13" aria-hidden="true">
            <circle cx="5.5" cy="6.5" r="5" fill="#1a1a1a"/>
            <path d="M3 4.5 Q5 3.5 6 5.5 Q5 7 3.5 7 Z M6.5 8 Q8.5 7.5 8.5 9.5 Q7 10.5 6.5 8 Z" fill="#f7f7f7"/>
          </svg>
          www.lumadrift.com
        </li>
      </ul>
    </div>
    <div class="front-band"></div>
  </section>

  <section class="card card--back">
    <div class="back-mark">LUMA</div>
    <p class="back-url">WWW.LUMADRIFT.COM</p>
  </section>
</main>
</body>
</html>
```